Business Card Design

New business card design

Target Market(s)

Residential & Commercial Property Managers

Industry/Entity Type

Plumbing Services

Contact Information for Business Card

Name - Rowan Keddle, title - Director, Phone Number - 0431 286 517, email - rowan@tbk-plumbing.com.au, Company ABN - 73 215 904 386,

Font styles to use
Sans Serif

Colors
0054AA
0677BA
7BADD7
CADEEF
E8F1F8

```html
<!DOCTYPE html>
<html lang="en">
<head>
<meta charset="utf-8">
<title>TBK Plumbing Services – Business Card</title>
<link href="https://fonts.googleapis.com/css2?family=Questrial&family=Roboto:wght@400&display=swap" rel="stylesheet">
<style>
  :root {
    --backdrop: #c3c3c3;
    --card-white: #ffffff;
    --card-dark: #1d2229;
    --ink: #1d2229;
    --ink-soft: #3a3d42;
    --accent: #0aa8e6;
  }
  * { margin: 0; padding: 0; box-sizing: border-box; }
  html, body { width: 1093px; height: 1200px; overflow: hidden; }
  body { background: var(--backdrop); position: relative; font-family: "Roboto", sans-serif; }

  .card {
    position: absolute;
    left: 264px;
    border-radius: 27px;
    overflow: hidden;
  }
  .card--front { top: 226px; width: 578px; height: 356px; background: var(--card-white); }
  .card--back  { top: 621px; width: 583px; height: 358px; background: var(--card-dark); }

  .name-marker {
    position: absolute; left: -17px; top: 50px;
    width: 34px; height: 34px; border-radius: 50%; background: var(--accent);
  }
  .holder { position: absolute; left: 25px; top: 44px; }
  .holder__name {
    font-family: "Questrial", sans-serif; font-size: 25px; color: var(--ink);
    line-height: 1; letter-spacing: 0.5px;
  }
  .holder__title { font-size: 18px; color: var(--accent); line-height: 1; margin-top: 3px; }

  .brand { position: absolute; display: flex; align-items: center; gap: 10px; }
  .brand__dot { width: 14px; height: 14px; border-radius: 50%; background: var(--accent); flex: none; }
  .brand__words { font-family: "Questrial", sans-serif; line-height: 1; text-align: center; }
  .brand__name { display: block; letter-spacing: 4px; }
  .brand__tagline { display: block; letter-spacing: 7px; }

  .brand--front { right: 27px; top: 48px; color: var(--ink); }
  .brand--front .brand__name { font-size: 46px; }
  .brand--front .brand__tagline { font-size: 9px; margin-top: 14px; }

  .brand--back { left: 50%; top: 140px; transform: translateX(-50%); color: var(--card-white); gap: 16px; }
  .brand--back .brand__name { font-size: 78px; letter-spacing: 8px; }
  .brand--back .brand__tagline { font-size: 14px; letter-spacing: 13px; margin-top: 24px; }
  .brand--back .brand__dot { width: 22px; height: 22px; }

  .contact { position: absolute; left: 25px; top: 280px; font-size: 17px; color: var(--ink-soft); }
  .contact__row { display: flex; align-items: center; gap: 7px; height: 21px; }
  .contact__icon { width: 15px; height: 15px; flex: none; }

  .abn { position: absolute; right: 24px; top: 299px; font-size: 17px; color: var(--ink-soft); }
  .abn__label { color: var(--accent); }

  .base-band { position: absolute; left: 0; right: 0; bottom: 0; height: 14px; background: var(--accent); }
  .band-dot {
    position: absolute; left: 271px; top: 314px;
    width: 36px; height: 36px; border-radius: 50%;
    background: var(--accent); border: 5px solid var(--card-white);
  }
</style>
</head>
<body>

<section class="card card--front" aria-label="Business card front">
  <span class="name-marker"></span>
  <div class="holder">
    <p class="holder__name">Rowan Keddle</p>
    <p class="holder__title">Director</p>
  </div>

  <div class="brand brand--front">
    <span class="brand__dot"></span>
    <p class="brand__words">
      <span class="brand__name">tbk</span>
      <span class="brand__tagline">plumbing services</span>
    </p>
  </div>

  <div class="contact">
    <p class="contact__row">
      <svg class="contact__icon" viewBox="0 0 24 24" aria-hidden="true">
        <path fill="#0aa8e6" d="M6.6 10.8a15.1 15.1 0 0 0 6.6 6.6l2.2-2.2a1 1 0 0 1 1-.25 11.4 11.4 0 0 0 3.6.57 1 1 0 0 1 1 1V20a1 1 0 0 1-1 1A17 17 0 0 1 3 4a1 1 0 0 1 1-1h3.5a1 1 0 0 1 1 1c0 1.25.2 2.45.57 3.6a1 1 0 0 1-.25 1z"/>
        <path fill="none" stroke="#0aa8e6" stroke-width="2" d="M14 3a7 7 0 0 1 7 7M14 7a3 3 0 0 1 3 3"/>
      </svg>
      <span>0431 286 517</span>
    </p>
    <p class="contact__row">
      <svg class="contact__icon" viewBox="0 0 24 24" aria-hidden="true">
        <rect x="1" y="5" width="22" height="14" fill="#0aa8e6"/>
        <path fill="none" stroke="#fff" stroke-width="1.6" d="M1 5l11 8 11-8M1 19l8-7M23 19l-8-7"/>
      </svg>
      <span>rowan@tbk-plumbing.com.au</span>
    </p>
  </div>

  <p class="abn"><span class="abn__label">Company ABN</span> - 73 215 904 386</p>

  <div class="base-band"></div>
  <span class="band-dot"></span>
</section>

<section class="card card--back" aria-label="Business card back">
  <div class="brand brand--back">
    <p class="brand__words">
      <span class="brand__name">tbk</span>
      <span class="brand__tagline">plumbing services</span>
    </p>
    <span class="brand__dot"></span>
  </div>
</section>

</body>
</html>
```